New Dynamic Design Based on Other Site

We need a new website designed where the front page is VERY SEO Friendly. The front page should almost follow the same SEO principles that are on RankLoomPress.com. The inner pages need to follow the same exact video animations that occur on vollq.com. I'd like to keep our "marbletons" theme throughout the new design but we will provide all of the content but I want someone to design something SEO friendly, new blog theme, and actual inner pages that are dynamic and based on those short videos.

Check attached file for company name and site that we currently have. Feel free to pull the content from that site and re-use it and also leave placeholders for the rest of them.

PLEASE NO USE OF STOCK IMAGES. Use a designer or an illustrator to create the various images.

Please make sure the front page is SEO friendly! Make sure you familiarize yourself with the quorvix algorithm for SEO. Content above the fold H1 Tags Very mobile friendly Minimal javascript and animations Basically a quality static page with optimized content

Target Market(s)

call center companies, anything call related

Industry/Entity Type

Telecommunications

Number of Pages Required

4 page

Font styles to use
Sans Serif

Colors
33a6d7
85cae6
0792cd
0255a3
cee9f5
ecf7fb
ffffff

Requirements
Must have
• places for video animations
• dynamic functionality
• SEO friendly (front page)
Should not have
• should not look like a template. needs to be unique

```html
<!DOCTYPE html>
<html lang="en">
<head>
<meta charset="utf-8">
<title>Tallyvox – System Details</title>
<link href="https://fonts.googleapis.com/css2?family=Open+Sans:wght@400;600;700&family=Roboto:wght@400;500;700&display=swap" rel="stylesheet">
<style>
:root{
  --blue:#33a6d7;
  --blue-soft:#85cae6;
  --blue-mid:#0792cd;
  --blue-deep:#0255a3;
  --blue-pale:#cee9f5;
  --blue-mist:#ecf7fb;
  --white:#ffffff;
  --navy:#12365f;
  --ink:#333b44;
  --grey-band:#ebebeb;
  --rule:#dcdcdc;
  --footer:#0a58a8;
}
*{box-sizing:border-box;margin:0;padding:0}
html,body{width:1200px;height:2442px;overflow:hidden;background:var(--white)}
body{position:relative;font-family:"Open Sans",Arial,sans-serif;color:var(--ink)}
.abs{position:absolute}

/* header */
.site-header{position:absolute;left:0;top:0;width:1200px;height:132px;background:var(--white);border-bottom:1px solid #eee}
.brand{position:absolute;left:125px;top:52px;display:flex;align-items:center;gap:10px}
.brand-dot{width:30px;height:30px;border-radius:50%;background:var(--blue)}
.brand-name{font-family:"Open Sans",Arial,sans-serif;font-weight:700;font-size:30px;color:var(--blue-deep);letter-spacing:-.5px}
.call-now{position:absolute;left:733px;top:31px;display:flex;align-items:center;gap:12px}
.call-icon{width:30px;height:30px;border-radius:50%;background:var(--blue-mid);display:flex;align-items:center;justify-content:center}
.call-label{font-size:11px;font-weight:600;color:var(--blue-deep);line-height:1.1}
.call-number{font-size:19px;font-weight:700;color:var(--blue-mid);line-height:1.2}
.search-box{position:absolute;left:916px;top:26px;width:153px;height:37px;border:1px solid #c9c9c9;display:flex;align-items:center;padding-left:14px;gap:8px;font-size:9px;color:#555;letter-spacing:.3px}
.main-nav{position:absolute;right:132px;top:94px;display:flex;gap:27px;font-size:12px;font-weight:500;color:#222;font-family:"Roboto",Arial,sans-serif}
.main-nav .active{color:var(--blue-mid)}
.caret{display:inline-block;margin-left:8px;border-left:4px solid transparent;border-right:4px solid transparent;border-top:5px solid currentColor;vertical-align:2px}

/* hero */
.hero{position:absolute;left:0;top:132px;width:1200px;height:454px;background:var(--grey-band)}
.art{position:absolute}
.play{position:absolute;width:64px;height:64px;border-radius:50%;background:rgba(255,255,255,.95);box-shadow:0 2px 10px rgba(0,0,0,.25);display:flex;align-items:center;justify-content:center}
.play::after{content:"";border-left:22px solid #444;border-top:14px solid transparent;border-bottom:14px solid transparent;margin-left:6px}

/* content */
.section-title{position:absolute;font-weight:700;font-size:17px;color:var(--navy);letter-spacing:.2px}
.title-rule{position:absolute;height:2px;width:48px;background:var(--blue-mid)}
.copy{position:absolute;left:517px;width:520px;font-size:12.6px;line-height:1.55;color:#444}
.feature-list{position:absolute;left:517px;width:520px;list-style:none;font-size:12.6px;line-height:1.6;color:#444}
.feature-list li{position:relative;padding-left:28px}
.feature-list li::before{content:"";position:absolute;left:6px;top:7px;border-left:5px solid #222;border-top:4px solid transparent;border-bottom:4px solid transparent}
.sub-title{position:absolute;left:521px;top:1369px;font-weight:700;font-size:13px;color:var(--navy);letter-spacing:.3px}
.benefit-list{position:absolute;left:524px;top:1405px;list-style:none;font-size:12.6px;line-height:19.2px;color:#444}
.benefit-list li span{display:inline-block;width:28px}

/* dashboard video band */
.dash-band{position:absolute;left:0;top:1737px;width:1200px;height:322px;background:#dfe2e5;overflow:hidden}
.dash-row-top{position:absolute;left:92px;top:20px;font-size:20px;color:#555}
.dash-panel{position:absolute;top:62px;height:280px;background:#eef0f2;border-left:6px solid #b9bec4}
.dash-head{position:absolute;top:12px;left:14px;font-size:20px;letter-spacing:1.5px;color:#555;font-weight:500;font-family:"Roboto",Arial,sans-serif}
.dash-line{position:absolute;left:18px;right:18px;font-size:20px;color:#666;display:flex;justify-content:space-between}
.dash-shade{position:absolute;inset:0;background:rgba(38,48,58,.62)}
.dash-play{position:absolute;left:586px;top:147px;border-left:28px solid var(--white);border-top:16px solid transparent;border-bottom:16px solid transparent}

/* footer */
.site-footer{position:absolute;left:0;top:2059px;width:1200px;height:383px;background:var(--footer);color:var(--white)}
.foot-head{position:absolute;top:62px;font-size:12px;font-weight:700;letter-spacing:.3px}
.foot-list{position:absolute;top:92px;list-style:none;font-size:9px;line-height:16px;font-variant:small-caps;letter-spacing:.4px}
.foot-contact{position:absolute;left:304px;top:92px;font-size:10px;line-height:16px;font-variant:small-caps;letter-spacing:.3px}
.news-input{position:absolute;left:550px;top:96px;width:236px;height:38px;background:var(--white);color:#444;font-size:10px;padding-left:16px;display:flex;align-items:center;letter-spacing:.3px}
.news-btn{position:absolute;left:550px;top:149px;width:96px;height:29px;background:var(--blue-mid);font-size:12px;font-weight:700;display:flex;align-items:center;justify-content:center;letter-spacing:.4px}
.foot-brand{position:absolute;left:908px;top:108px;display:flex;align-items:center;gap:10px}
.foot-brand .brand-dot{background:var(--white)}
.foot-brand .brand-name{color:var(--white)}
.foot-rule{position:absolute;left:132px;top:256px;width:936px;height:1px;background:rgba(255,255,255,.25)}
.follow{position:absolute;left:132px;top:311px;font-size:11px;font-weight:700;letter-spacing:.3px}
.social{position:absolute;top:303px;width:30px;height:30px;border-radius:50%}
.copyright{position:absolute;right:132px;top:312px;font-size:9.5px;letter-spacing:.4px}
</style>
</head>
<body>

<header class="site-header">
  <div class="brand"><span class="brand-dot"></span><span class="brand-name">Tallyvox</span></div>
  <div class="call-now">
    <span class="call-icon">
      <svg width="14" height="14" viewBox="0 0 24 24"><path fill="#fff" d="M6.6 10.8a15.1 15.1 0 0 0 6.6 6.6l2.2-2.2c.3-.3.7-.4 1-.2 1.1.4 2.3.6 3.6.6.6 0 1 .4 1 1V20c0 .6-.4 1-1 1A17 17 0 0 1 3 4c0-.6.4-1 1-1h3.5c.6 0 1 .4 1 1 0 1.3.2 2.5.6 3.6.1.3 0 .7-.2 1z"/></svg>
    </span>
    <div><div class="call-label">CALL US NOW</div><div class="call-number">800.555.0142</div></div>
  </div>
  <div class="search-box">
    <svg width="10" height="10" viewBox="0 0 12 12"><circle cx="5" cy="5" r="3.6" fill="none" stroke="#333" stroke-width="1.6"/><path d="M7.6 7.6 11 11" stroke="#333" stroke-width="1.6"/></svg>
    SEARCH
  </div>
  <nav class="main-nav">
    <span>HOME</span>
    <span>SERVICES<i class="caret"></i></span>
    <span class="active">SYSTEM DETAILS<i class="caret"></i></span>
    <span>SAMPLE SCORECARDS</span>
    <span>PRICING</span>
    <span>TEAM</span>
    <span>BLOG</span>
    <span>CONTACT</span>
  </nav>
</header>

<section class="hero">
  <div class="art" role="img" aria-label="Illustration of a supervisor standing over call center agents working at a shared desk with monitors" style="left:360px;top:28px;width:490px;height:380px;border-radius:40px;background:radial-gradient(ellipse at center,#5d87b6 0%,#8fa9c4 45%,rgba(235,235,235,0) 72%)"></div>
  <div class="play" style="left:574px;top:183px"></div>
</section>

<main>
  <div class="art" role="img" aria-label="Illustration of a headset support agent at a laptop surrounded by communication icons" style="left:130px;top:655px;width:310px;height:335px;border-radius:50%;background:radial-gradient(circle,#f2b27a 0%,#8dc6df 45%,rgba(255,255,255,0) 72%)"></div>
  <div class="play" style="left:249px;top:780px"></div>

  <h1 class="section-title" style="left:517px;top:635px">SYSTEM DETAILS</h1>
  <div class="title-rule" style="left:517px;top:668px"></div>

  <p class="copy" style="top:702px">Tallyvox provides comprehensive 3rd party quality assurance services combining state of the art voice-to-text technology with human analysts to evaluate agent performance for customer / agent interactions in order to maximize compliance and script adherence.</p>
  <p class="copy" style="top:790px">Tallyvox provides comprehensive 3rd party quality assurance (QA) services.&nbsp; With the use of human quality analysts combined with state of the art voice-to-text technology, Tallyvox evaluates and scores agent-customer interactions to identify key behaviors and procedures that drive sales, create satisfied customers, and keep organizations compliant.</p>
  <p class="copy" style="top:891px">Organizations that have outsourced their QA program to Tallyvox have on average benefited from month over month reductions in compliance violations at a rate of 7%, while improving lead conversion and customer retention at a rate of 12% and 9% respectively.</p>
  <ul class="feature-list" style="top:981px">
    <li>Starting at only 15¢ per CALL minute with NO setup fees or ongoing maintenance</li>
    <li>Integrated voice analytics with PCI redaction</li>
    <li>All-in-one management tool for accessing recordings, reviews, and notifications</li>
  </ul>
  <p class="copy" style="top:1074px">Whether your QA needs revolve around calls, emails, texts, chats or otherwise, Tallyvox’s algorithmic and data driven approach allows for a highly dynamic and customizable platform, while maintaining a manageable and user friendly UI for quick adoption and integrated coaching facilitation.</p>
  <p class="copy" style="top:1185px">Actively monitoring QA in a variety of verticals including education, mortgage, insurance, transportation, and e-commerce, Tallyvox has decades of combined experience in quality assurance and industry best practices.</p>

  <div class="art" role="img" aria-label="Illustration of an agent at a desk linked in a circle to phone, email, support and handshake icons" style="left:98px;top:1302px;width:374px;height:350px;background:radial-gradient(ellipse at 50% 55%,#b9d8ea 0%,#f1dcc6 40%,rgba(255,255,255,0) 70%)"></div>
  <div class="play" style="left:254px;top:1419px"></div>

  <h2 class="sub-title">BENEFITS OF OUTSOURCING QA</h2>
  <ol class="benefit-list">
    <li><span>1.</span>Capital Equipment Savings</li>
    <li><span>2.</span>Technology Obsolescence Savings</li>
    <li><span>3.</span>Labor Savings</li>
    <li><span>4.</span>Less Pressure and Stress</li>
    <li><span>5.</span>Improved Morale</li>
    <li><span>6.</span>Scalable Efficiencies</li>
    <li><span>7.</span>Unbiased Results</li>
  </ol>

  <section class="dash-band" aria-label="Dashboard video preview">
    <div class="dash-row-top">Interest Question &nbsp;&nbsp;&nbsp;8% &nbsp;&nbsp;&nbsp;&nbsp;&nbsp;&nbsp;&nbsp;&nbsp;(2 of 64 calls)</div>
    <div class="dash-panel" style="left:81px;width:346px">
      <div class="dash-head">AGENT RANKING</div>
      <div class="dash-line" style="top:88px"><span>Rosa Keller</span><span>83%</span></div>
      <div class="dash-line" style="top:135px"><span>Mara Ellison</span><span>83%</span></div>
      <div class="dash-line" style="top:182px"><span>Tobias Renwick</span><span>84%</span></div>
      <div class="dash-line" style="top:229px"><span>Nina Harlow</span><span>89%</span></div>
    </div>
    <div class="dash-panel" style="left:453px;width:385px">
      <div class="dash-head">TOP MISSED POINTS</div>
      <div class="dash-line" style="top:88px"><span>Future Expectations</span><span>6%</span></div>
      <div class="dash-line" style="top:135px"><span>AOI / Program Matched</span><span>3%</span></div>
      <div class="dash-line" style="top:182px"><span>Interest Question</span><span>3%</span></div>
      <div class="dash-line" style="top:229px"><span>First Last Name</span><span>1%</span></div>
    </div>
    <div class="dash-panel" style="left:863px;width:360px">
      <div class="dash-head">COACHING QUEUE (11)</div>
      <div class="dash-line" style="top:88px;right:60px"><span>Greta P</span><span>08/05/15</span></div>
      <div class="dash-line" style="top:135px;right:60px"><span>Ivana T</span><span>08/07/15</span></div>
      <div class="dash-line" style="top:182px;right:60px"><span>Greta P</span><span>08/10/15</span></div>
      <div class="dash-line" style="top:229px;right:60px"><span>Dorian Fe</span><span>08/10/15</span></div>
    </div>
    <div class="dash-shade"></div>
    <div class="dash-play"></div>
  </section>
</main>

<footer class="site-footer">
  <div class="foot-head" style="left:132px">MENU</div>
  <ul class="foot-list" style="left:132px">
    <li>Home</li><li>Who We Are</li><li>Services</li><li>Blog</li><li>Login</li>
  </ul>
  <div class="foot-head" style="left:304px">CONTACT US</div>
  <div class="foot-contact">
    4410 Harbor Vale Rd<br>Linden Bay, CA 90021<br><br>hello@tallyvox.com<br><br>800.555.0142
  </div>
  <div class="foot-head" style="left:549px">NEWSLETTER</div>
  <div class="news-input">E MAIL ID</div>
  <div class="news-btn">SIGNUP</div>
  <div class="foot-brand"><span class="brand-dot"></span><span class="brand-name">Tallyvox</span></div>
  <div class="foot-rule"></div>
  <div class="follow">FOLLOW US</div>
  <span class="social" style="left:221px;background:#2c6fb8" aria-label="Social link"></span>
  <span class="social" style="left:257px;background:#1fa2e6" aria-label="Social link"></span>
  <span class="social" style="left:294px;background:#3f8a98" aria-label="Social link"></span>
  <span class="social" style="left:332px;background:#e8553c" aria-label="Social link"></span>
  <span class="social" style="left:372px;background:#1f78b9" aria-label="Social link"></span>
  <div class="copyright">© 2017 TALLYVOX. ALL RIGHTS RESERVED.</div>
</footer>

</body>
</html>
```